Oil Field Service company needs professional business cards

Looking to clean up our current company business cards and look a little more professional. Brenwick Casing Services is a US based company that services the oil field. We deal with engineers, managers and oil rigs....................................................................................................................................................................................................................................................................................................................................................................................................

Target Market(s)

Oil and Gas professionals

Industry/Entity Type

Oil And Gas

Contact Information for Business Card

See attached photo as example

Font styles to use
Sans Serif

Colors
ec1f27

Requirements
Must have
• Company Logo, Name, Title, Cell, Office, Fax, Email.
• See attached photo
Nice to have
• External CRT, Internal CRT, Casing Crews, Torque Turn, Laydown Machine
Should not have
• Do not introduce any new pictures and keep it professional looking

```html
<!DOCTYPE html>
<html lang="en">
<head>
<meta charset="utf-8">
<title>Brenwick Casing Services – Business Card</title>
<link rel="stylesheet" href="https://fonts.googleapis.com/css2?family=Oswald:wght@400;500;600&display=swap">
<style>
  :root {
    --red: #d3201f;
    --red-dark: #bf1b1b;
    --navy: #3d4f5f;
    --ink: #333b44;
    --paper: #f7f7f5;
    --backdrop: #e8e8e8;
  }
  * { margin: 0; padding: 0; box-sizing: border-box; }
  html, body {
    width: 1200px; height: 576px; overflow: hidden;
    background: var(--backdrop);
    font-family: "Oswald", sans-serif;
  }
  .canvas { position: relative; width: 1200px; height: 576px; }
  .card {
    position: absolute;
    width: 484px; height: 292px;
    border-radius: 7px;
    overflow: hidden;
  }
  /* Front */
  .card-front {
    left: 82px; top: 139px;
    background: linear-gradient(180deg, var(--red) 0%, var(--red-dark) 100%);
    color: #fff;
    display: flex; flex-direction: column; align-items: center; justify-content: center;
  }
  .wordmark { font-weight: 600; line-height: 1; text-align: center; }
  .card-front .wordmark-name { font-size: 50px; letter-spacing: 1px; }
  .card-front .wordmark-tag { font-size: 15px; letter-spacing: 3px; margin-top: 10px; }
  /* Back */
  .card-back { left: 602px; top: 138px; background: var(--paper); color: var(--ink); }
  .card-back .wordmark { position: absolute; left: 26px; top: 44px; color: var(--navy); text-align: center; }
  .card-back .wordmark-name { font-size: 46px; letter-spacing: 1px; }
  .card-back .wordmark-tag { font-size: 13px; letter-spacing: 2.6px; margin-top: 8px; }
  .holder { position: absolute; right: 24px; top: 134px; text-align: right; }
  .holder-name { font-size: 22px; font-weight: 500; color: var(--ink); line-height: 1.1; }
  .holder-title { font-size: 11.5px; font-weight: 400; color: #444; margin-top: 4px; }
  .rule { position: absolute; left: 26px; top: 169px; width: 344px; height: 1px; background: var(--red); }
  .contact { position: absolute; list-style: none; font-size: 12px; }
  .contact li { display: flex; align-items: center; height: 16px; }
  .contact svg { width: 10px; height: 10px; margin-right: 9px; fill: var(--red); flex: none; }
  .contact-phones { left: 30px; top: 199px; }
  .contact-place { left: 281px; top: 198px; }
  .band-red { position: absolute; left: 0; bottom: 0; width: 270px; height: 16px; background: var(--red); }
  .band-navy { position: absolute; right: 0; bottom: 0; width: 230px; height: 35px; }
  .web {
    position: absolute; right: 0; bottom: 0; width: 210px; height: 35px;
    display: flex; align-items: center; justify-content: center;
    color: #fff; font-size: 12px;
  }
</style>
</head>
<body>
<main class="canvas">
  <section class="card card-front" aria-label="Card front">
    <div class="wordmark">
      <div class="wordmark-name">BRENWICK</div>
      <div class="wordmark-tag">CASING SERVICES</div>
    </div>
  </section>

  <section class="card card-back" aria-label="Card back">
    <div class="wordmark">
      <div class="wordmark-name">BRENWICK</div>
      <div class="wordmark-tag">CASING SERVICES</div>
    </div>

    <div class="holder">
      <div class="holder-name">Cole Harlan</div>
      <div class="holder-title">Area Manager</div>
    </div>
    <div class="rule"></div>

    <ul class="contact contact-phones">
      <li><svg viewBox="0 0 10 10" aria-hidden="true"><path d="M2 0.5 3.6 2.6 2.7 3.6Q3.6 5.8 6.4 7.3L7.4 6.4 9.5 8 8.4 9.5Q3.5 8.7 0.5 1.6Z"/></svg>(580) 555-0142</li>
      <li><svg viewBox="0 0 10 10" aria-hidden="true"><path d="M0 3.2Q5-0.8 10 3.2L9.2 4.4 7.4 3.8 7.3 2.8Q5 2 2.7 2.8L2.6 3.8 0.8 4.4Z M2 5 8 5 9.2 9.5 0.8 9.5Z"/></svg>(580) 555-0187</li>
      <li><svg viewBox="0 0 10 10" aria-hidden="true"><path d="M2.5 0.5H7.5V3H2.5Z M0.5 3.6H9.5V7.5H8V6H2V7.5H0.5Z M2.6 6.6H7.4V9.5H2.6Z"/></svg>(580) 555-0163</li>
    </ul>

    <ul class="contact contact-place">
      <li><svg viewBox="0 0 10 10" aria-hidden="true"><path d="M5 0A3.6 3.6 0 0 0 1.4 3.6C1.4 6 5 10 5 10S8.6 6 8.6 3.6A3.6 3.6 0 0 0 5 0ZM5 5.1A1.5 1.5 0 1 1 5 2.1 1.5 1.5 0 0 1 5 5.1Z"/></svg>Alder Springs, OK 73990</li>
      <li><svg viewBox="0 0 10 10" aria-hidden="true"><path d="M0.5 2H9.5V2.6L5 5.6 0.5 2.6Z M0.5 3.6 5 6.6 9.5 3.6V8.2H0.5Z"/></svg>coleharlan@brenwickcs.com</li>
    </ul>

    <div class="band-red"></div>
    <svg class="band-navy" viewBox="0 0 230 35" preserveAspectRatio="none" aria-hidden="true">
      <polygon points="16,0 230,0 230,35 0,35" fill="var(--navy)"/>
    </svg>
    <div class="web">www.brenwickcs.com</div>
  </section>
</main>
</body>
</html>
```